Basic / Quick Business Card

Quick easy design project!

Need a one sided basic business card that matches font & style of brand and bottle label for our gourmet condiment, Brindle Harrow Sauce. Brindle Harrow Sauce is sold in specialty retail, gourmet groceries and appears on chef-driven restaurant menus, so the target market is a high end, gourmet, artisan-made food-loving customer.

Files Included:
Sauce Bottle Label
Brindle Harrow Sauce Round Logos

**About the logos - the logo may be used in a circle or alone vertically as on side of the bottle label**

Layout of Card:
May be vertical or horizontal based on designer ideas.

Logo usage (in circle vs. stand alone vertical logo) is up to designers descretion as well.

Reverse side of business card will be various high end / professional product photos / food shots using us.kelbo.com system. **Designer on this project will NOT design a reserve for the card.**

Paper that will be used for printing:
Kelbo Standard - it's a WHITE paper, but we use a cream background on Brindle Harrow Sauce branding, so please take this into account on design to stay brand consistent.

Elements & Copy for Card:
1. Logo in either script horizontal or vertical version
2. Copy: "Artisan Made - Small Batch"
3. Name - Wes Dorrance
4. Title - Creator
5. Phone - xxx.xxx.xxxx
6. xxxx@brindleharrow.com
7. URL: brindleharrowsauce.com
8. Social Media: @getbrindleharrow on Quillo / Pagora / Lumigrid

Please provide final files in Illustrator or InDesign format.

```html
<!DOCTYPE html>
<html lang="en">
<head>
<meta charset="utf-8">
<title>Brindle Harrow Sauce – Business Card</title>
<link rel="stylesheet" href="https://fonts.googleapis.com/css2?family=Alegreya+Sans:wght@400;500&family=Alegreya:wght@400&display=swap">
<style>
  :root {
    --backdrop: #d9d4cc;
    --card: #ffffff;
    --ink: #231f20;
    --band: #231f20;
    --gold: #f0b21a;
    --cream: #eceadb;
    --rule: #bdbdbd;
    --on-band: #ffffff;
  }
  * { margin: 0; padding: 0; box-sizing: border-box; }
  html, body {
    width: 1200px; height: 804px; overflow: hidden;
    background: var(--backdrop);
  }
  .card {
    position: absolute; left: 100px; top: 116px;
    width: 1000px; height: 572px;
    background: var(--card);
    box-shadow: 0 6px 18px rgba(0,0,0,.18);
    overflow: hidden;
    font-family: "Alegreya", Georgia, serif;
    color: var(--ink);
  }
  .card-art { position: absolute; inset: 0; width: 100%; height: 100%; }
  .holder {
    position: absolute; right: 70px; top: 66px;
    text-align: right; color: var(--on-band);
    font-family: "Alegreya Sans", Arial, sans-serif; font-weight: 400;
    letter-spacing: .5px;
  }
  .holder-name { font-size: 38px; line-height: 1.15; }
  .holder-title { font-size: 36px; line-height: 1.15; }

  .brand-mark {
    position: absolute; left: 72px; top: 82px;
    width: 252px; height: 252px; border-radius: 50%;
    background: var(--cream);
    border: 12px solid var(--ink);
    display: flex; align-items: center; justify-content: center;
    text-align: center;
  }
  .brand-name {
    font-family: "Alegreya", Georgia, serif; font-weight: 400;
    font-size: 38px; line-height: 1.05; color: var(--ink);
  }

  .contact {
    position: absolute; left: 40px; top: 378px;
    font-size: 27px; line-height: 45px;
  }
  .contact-row { display: flex; align-items: center; gap: 10px; }
  .contact-row svg { width: 24px; height: 24px; flex: none; }
  .follow { font-family: "Alegreya Sans", Arial, sans-serif; font-size: 27px; }
  .divider {
    position: absolute; left: 432px; top: 392px;
    width: 2px; height: 150px; background: var(--rule);
  }
  .tagline {
    position: absolute; left: 458px; top: 400px;
    font-size: 27px; line-height: 38px;
  }
</style>
</head>
<body>
  <div class="card">
    <svg class="card-art" viewBox="0 0 1000 572" aria-hidden="true">
      <path d="M300 0 H1000 V440 C865 205 590 55 300 0 Z" fill="var(--band)"/>
      <path d="M0 60 C420 38 860 190 1000 468 L1000 548 C880 270 470 72 0 68 Z" fill="var(--gold)"/>
    </svg>

    <div class="holder">
      <div class="holder-name">Wes Dorrance</div>
      <div class="holder-title">Creator</div>
    </div>

    <div class="brand-mark">
      <span class="brand-name">Brindle<br>Harrow<br>Sauce</span>
    </div>

    <div class="contact">
      <div class="contact-row">
        <svg viewBox="0 0 24 24"><circle cx="12" cy="12" r="11" fill="none" stroke="var(--ink)" stroke-width="2"/><path d="M8 6 L10.5 6 L11.5 9 L10 10.3 C10.8 12 12 13.2 13.7 14 L15 12.5 L18 13.5 L18 16 C12 17 7 12 8 6 Z" fill="var(--ink)"/></svg>
        <span>123-456-7890</span>
      </div>
      <div class="contact-row">
        <svg viewBox="0 0 24 24"><circle cx="12" cy="12" r="11" fill="var(--ink)"/><rect x="6" y="8" width="12" height="8.5" fill="#fff"/><path d="M6 8 L12 13 L18 8" fill="none" stroke="var(--ink)" stroke-width="1.4"/></svg>
        <span>wdorrance@brindleharrow.com</span>
      </div>
      <div class="contact-row">
        <svg viewBox="0 0 24 24"><circle cx="12" cy="12" r="10" fill="none" stroke="var(--ink)" stroke-width="2"/><ellipse cx="12" cy="12" rx="4.5" ry="10" fill="none" stroke="var(--ink)" stroke-width="1.5"/><path d="M2 12 H22 M4 7 H20 M4 17 H20" stroke="var(--ink)" stroke-width="1.5"/></svg>
        <span>www.brindleharrowsauce.com</span>
      </div>
      <div class="contact-row follow">
        <span>Follow Us On Pagora · Quillo · Lumigrid</span>
      </div>
    </div>

    <div class="divider"></div>

    <div class="tagline">
      <div>sweet &amp; spicy</div>
      <div>Artisan Made - Small Batch</div>
    </div>
  </div>
</body>
</html>
```